VOMRA Pty Ltd Business Card

Looking for a simple yet eye-catching double-sided business card design using my company logo on one side and contact details on the other.

Target Market(s)

Government

Industry/Entity Type

Communication Systems Engineering

Contact Information for Business Card

VOMRA Pty Ltd

Requirements
Nice to have
• Would be great to have a QR code so details can be scanned into contacts

```html
<!DOCTYPE html>
<html lang="en">
<head>
<meta charset="utf-8">
<title>VOMRA Pty Ltd Business Card</title>
<link href="https://fonts.googleapis.com/css2?family=Montserrat:wght@700&family=Open+Sans:wght@400;700&display=swap" rel="stylesheet">
<style>
  :root {
    --backdrop: #232323;
    --card: #ffffff;
    --ink: #333d44;
    --text: #1e1e1e;
    --muted: #555b60;
  }
  * { box-sizing: border-box; margin: 0; padding: 0; }
  html, body { width: 1200px; height: 780px; overflow: hidden; }
  body {
    background: var(--backdrop);
    font-family: "Open Sans", sans-serif;
    display: flex;
    align-items: center;
    justify-content: center;
    gap: 40px;
  }
  .card {
    position: relative;
    width: 550px;
    height: 314px;
    background: var(--card);
    overflow: hidden;
    box-shadow: 0 12px 30px rgba(0,0,0,0.45);
  }
  .card-front {
    display: flex;
    align-items: center;
    justify-content: center;
  }
  .brand {
    font-family: "Montserrat", sans-serif;
    font-weight: 700;
    color: var(--ink);
    letter-spacing: 4px;
    display: flex;
    align-items: center;
  }
  .brand-front { font-size: 76px; gap: 22px; }
  .brand-mark {
    display: block;
    background: var(--ink);
  }
  .brand-front .brand-mark { width: 22px; height: 22px; }
  .brand-back {
    position: absolute;
    left: 34px;
    top: 40px;
    font-size: 40px;
    gap: 12px;
  }
  .brand-back .brand-mark { width: 12px; height: 12px; }
  .person {
    position: absolute;
    right: 36px;
    top: 86px;
    text-align: right;
  }
  .person-name {
    font-weight: 700;
    font-size: 27px;
    color: var(--ink);
    line-height: 1.1;
  }
  .person-role {
    font-size: 13px;
    color: var(--text);
    margin-top: 2px;
  }
  .accent-bar {
    position: absolute;
    right: 0;
    top: 82px;
    width: 16px;
    height: 58px;
    background: var(--ink);
  }
  .contact {
    position: absolute;
    left: 34px;
    bottom: 26px;
    color: var(--text);
    font-size: 13.5px;
    line-height: 1.35;
  }
  .address { margin-bottom: 10px; }
  .contact-list { list-style: none; }
  .contact-list li { display: flex; align-items: center; gap: 9px; }
  .contact-list svg { width: 13px; height: 13px; fill: var(--muted); flex: none; }
</style>
</head>
<body>
  <section class="card card-front" aria-label="Card front">
    <div class="brand brand-front"><span class="brand-mark"></span>VOMRA</div>
  </section>

  <section class="card card-back" aria-label="Card back">
    <div class="brand brand-back"><span class="brand-mark"></span>VOMRA</div>

    <div class="person">
      <p class="person-name">Dana Whitlock</p>
      <p class="person-role">Co-Founder</p>
    </div>
    <span class="accent-bar"></span>

    <div class="contact">
      <p class="address">14-16 Harlow Lane Eastvale<br>NSW 2099 Australia</p>
      <ul class="contact-list">
        <li>
          <svg viewBox="0 0 24 24" aria-hidden="true"><path d="M6.6 10.8a15.1 15.1 0 0 0 6.6 6.6l2.2-2.2a1 1 0 0 1 1-.25 11.4 11.4 0 0 0 3.6.57 1 1 0 0 1 1 1V20a1 1 0 0 1-1 1A17 17 0 0 1 3 4a1 1 0 0 1 1-1h3.5a1 1 0 0 1 1 1c0 1.25.2 2.45.57 3.6a1 1 0 0 1-.25 1z"/></svg>
          (555) 014-2290
        </li>
        <li>
          <svg viewBox="0 0 24 24" aria-hidden="true"><path d="M12 2a10 10 0 1 0 0 20 10 10 0 0 0 0-20zm6.9 6h-2.9a15.6 15.6 0 0 0-1.4-3.6A8 8 0 0 1 18.9 8zM12 4a14 14 0 0 1 1.9 4h-3.8A14 14 0 0 1 12 4zM4.3 14a8 8 0 0 1 0-4h3.4a16.5 16.5 0 0 0 0 4zm.8 2h2.9a15.6 15.6 0 0 0 1.4 3.6A8 8 0 0 1 5.1 16zM8 8H5.1a8 8 0 0 1 4.3-3.6A15.6 15.6 0 0 0 8 8zm4 12a14 14 0 0 1-1.9-4h3.8A14 14 0 0 1 12 20zm2.3-6H9.7a14.7 14.7 0 0 1 0-4h4.6a14.7 14.7 0 0 1 0 4zm.3 5.6a15.6 15.6 0 0 0 1.4-3.6h2.9a8 8 0 0 1-4.3 3.6zm1.7-5.6a16.5 16.5 0 0 0 0-4h3.4a8 8 0 0 1 0 4z"/></svg>
          www.vomra.com.au
        </li>
        <li>
          <svg viewBox="0 0 24 24" aria-hidden="true"><path d="M3 5h18a1 1 0 0 1 1 1v12a1 1 0 0 1-1 1H3a1 1 0 0 1-1-1V6a1 1 0 0 1 1-1zm9 7.2L4.4 7H19.6zM4 8.6V17h16V8.6l-8 5.5z"/></svg>
          admin@vomra.com.au
        </li>
      </ul>
    </div>
  </section>
</body>
</html>
```